Promotional business a5 Notepad design

I am looking for a custom a5 notepad design as a promotional item to give away to customers etc.
Attached will be a desk planner we had designed feel free to use as a reference.
We want the notepad to have lines running horizontal not squares like the desk planner example.

Industry/Entity Type

Hydraulic / industrial

Colors

Designer to choose colors to be used in the design.

```html
<!DOCTYPE html>
<html lang="en">
<head>
<meta charset="utf-8">
<title>Meridian Hose and Couplings – A5 Notepad</title>
<link rel="stylesheet" href="https://fonts.googleapis.com/css2?family=Roboto:wght@400;700&display=swap">
<style>
  :root {
    --backdrop: #dcdcdc;
    --paper: #f7f7f7;
    --brand-blue: #2b3fa0;
    --ink: #3a3a3a;
    --rule: #c6cde6;
    --footer-black: #141414;
    --footer-text: #ffffff;
  }
  * { margin: 0; padding: 0; box-sizing: border-box; }
  html, body {
    width: 1153px; height: 1200px; overflow: hidden;
    background: var(--backdrop);
    font-family: "Roboto", sans-serif;
  }
  .notepad {
    position: absolute; left: 160px; top: 20px;
    width: 832px; height: 1160px;
    background: var(--paper);
    overflow: hidden;
  }
  .brand {
    position: absolute; left: 58px; top: 98px;
    width: 370px;
    display: flex; align-items: center; gap: 14px;
  }
  .brand-dot {
    width: 64px; height: 64px; border-radius: 50%;
    background: var(--brand-blue);
    flex: none;
  }
  .brand-name {
    color: var(--brand-blue);
    font-weight: 700; font-size: 24px; line-height: 28px;
    letter-spacing: 0.5px;
    text-transform: uppercase;
    white-space: nowrap;
  }
  .brand-name span { display: block; }
  .contact {
    position: absolute; left: 485px; top: 66px;
    color: var(--ink); font-size: 16.5px; line-height: 20px;
  }
  .contact address { font-style: normal; margin-bottom: 6px; }
  .contact-row { display: flex; align-items: center; gap: 6px; height: 21.5px; white-space: nowrap; }
  .contact-row svg { width: 16px; height: 16px; fill: var(--brand-blue); flex: none; }
  .ruled-area {
    position: absolute; left: 54px; top: 243px;
    width: 721px; height: 817px;
    background: repeating-linear-gradient(to bottom,
      var(--rule) 0 1px, transparent 1px 34px);
  }
  .footer-stripe {
    position: absolute; left: 0; top: 1111px;
    width: 100%; height: 4px; background: var(--brand-blue);
  }
  .footer-band {
    position: absolute; left: 0; top: 1121px;
    width: 100%; height: 39px; background: var(--footer-black);
    display: flex; align-items: center; justify-content: center;
    color: var(--footer-text); font-size: 16px; letter-spacing: 2px;
  }
</style>
</head>
<body>
  <main class="notepad">
    <header class="brand">
      <span class="brand-dot"></span>
      <span class="brand-name"><span>Meridian</span><span>Hose and Couplings</span></span>
    </header>

    <section class="contact">
      <address>24 Calder Street,<br>Northfield SA 5085</address>
      <div class="contact-row">
        <svg viewBox="0 0 16 16" aria-hidden="true"><path d="M1 6c0-2 3-3.5 7-3.5S15 4 15 6v1.5h-3.5V6h-7v1.5H1z"/><path d="M3.5 8.5 5 6.5h6l1.5 2v5.5h-9z"/><circle cx="8" cy="10.5" r="1.6" fill="#f7f7f7"/></svg>
        <span>0400 123 456</span>
      </div>
      <div class="contact-row">
        <svg viewBox="0 0 16 16" aria-hidden="true"><path d="M4.5 1h7a1 1 0 0 1 1 1v12a1 1 0 0 1-1 1h-7a1 1 0 0 1-1-1V2a1 1 0 0 1 1-1zm1 2v9h5V3z"/><circle cx="8" cy="13.4" r="0.8" fill="#f7f7f7"/></svg>
        <span>08 8100 2040</span>
      </div>
      <div class="contact-row">
        <svg viewBox="0 0 16 16" aria-hidden="true"><path d="M1 4h14v1L8 9.5 1 5z"/><path d="M1 6.5 8 11l7-4.5V12H1z"/></svg>
        <span>email@meridianhose.com.au</span>
      </div>
    </section>

    <div class="ruled-area" aria-hidden="true"></div>

    <div class="footer-stripe" aria-hidden="true"></div>
    <footer class="footer-band">www.meridianhose.com.au</footer>
  </main>
</body>
</html>
```